KBT Business Cards

We require business cards for our business. We would like a matte black back to the card, with our logo centred in the middle. The front side of the card is open to design.

Target Market(s)

Clients looking for legal services (professional)

Industry/Entity Type

Legal

Contact Information for Business Card

Doran Kelbrath
Partner
Mobile: 0461 738 524
Email: doran@kbtlaw.co
Website: www.kbtlaw.co
Level 3, 118 Wendmore Street
Sydney NSW 2000

Font styles to use
Other font styles liked:
• Avenir

Colors
f04a50
ffffff
1b1b1b

Requirements
Must have
• Black back with logo included in the centre of the card.
• Our font is Avenir.

```html
<!DOCTYPE html>
<html lang="en">
<head>
<meta charset="utf-8">
<title>KBT Legal Business Cards</title>
<link rel="stylesheet" href="https://fonts.googleapis.com/css2?family=Roboto:wght@400;500;700&display=swap">
<style>
  :root {
    --stage: #d9d6d2;
    --crimson-top: #d5234e;
    --crimson-bottom: #a61e3a;
    --crimson: #c41f45;
    --matte-black: #1b1b1b;
    --white: #ffffff;
  }
  * { margin: 0; padding: 0; box-sizing: border-box; }
  html, body {
    width: 1200px;
    height: 900px;
    overflow: hidden;
    background: var(--stage);
    font-family: "Roboto", "Avenir", Arial, sans-serif;
  }
  .canvas {
    position: relative;
    width: 1200px;
    height: 900px;
  }
  .card {
    position: absolute;
    left: 330px;
    width: 556px;
    height: 343px;
    box-shadow: 2px 3px 6px rgba(0, 0, 0, 0.35);
  }
  .card-front {
    top: 90px;
    background: linear-gradient(to bottom, var(--crimson-top), var(--crimson-bottom));
    color: var(--white);
    text-align: center;
  }
  .card-back {
    top: 470px;
    width: 558px;
    background: var(--matte-black);
    display: flex;
    align-items: center;
    justify-content: center;
  }
  .contact-block {
    position: absolute;
    top: 86px;
    left: 0;
    right: 0;
    display: flex;
    flex-direction: column;
    align-items: center;
  }
  .person-name {
    font-size: 19px;
    font-weight: 700;
    letter-spacing: 0.3px;
    line-height: 22px;
  }
  .person-role {
    font-size: 15px;
    line-height: 16px;
    margin-left: 2px;
  }
  .rule {
    width: 142px;
    height: 1px;
    background: var(--white);
  }
  .rule-top { margin: 11px 0 6px; }
  .rule-bottom { margin: 6px 0 8px; }
  .contact-list {
    list-style: none;
    font-size: 16px;
    line-height: 20px;
  }
  .contact-list b { font-weight: 700; }
  .address {
    font-size: 16px;
    line-height: 20px;
  }
  .brand {
    display: flex;
    align-items: center;
    gap: 22px;
    margin-left: 8px;
  }
  .brand-mark {
    width: 40px;
    height: 40px;
    background: var(--crimson);
  }
  .brand-name {
    font-size: 34px;
    font-weight: 500;
    color: var(--white);
    letter-spacing: 0.5px;
  }
</style>
</head>
<body>
  <main class="canvas">
    <section class="card card-front" aria-label="Card front">
      <div class="contact-block">
        <h1 class="person-name">DORAN KELBRATH</h1>
        <p class="person-role">Partner</p>
        <div class="rule rule-top"></div>
        <ul class="contact-list">
          <li><b>M:</b> 0461 738 524</li>
          <li><b>E:</b> doran@kbtlaw.co</li>
          <li><b>W:</b> www.kbtlaw.co</li>
        </ul>
        <div class="rule rule-bottom"></div>
        <p class="address">Level 3, 118 Wendmore<br>Street, Sydney NSW 2000</p>
      </div>
    </section>

    <section class="card card-back" aria-label="Card back">
      <div class="brand">
        <span class="brand-mark"></span>
        <span class="brand-name">KBT LEGAL</span>
      </div>
    </section>
  </main>
</body>
</html>
```